Building company needs a new logo and letterhead design

We need a new and refreshed logo and letterhead design for an existing building company. We specialise in residential as well as commercial building/construction, design and project management. Our company name is Vendaro Constructions Pty Ltd. Our primary colours that we want to use are black/orange/white. We do renovations/alterations/new homes both residential and commercial. We are a medium sized building company. We want something simple and modern.

Industry/Entity Type

Residential

```html
<!DOCTYPE html>
<html lang="en">
<head>
<meta charset="utf-8">
<title>Vendaro Constructions Pty Ltd – Letterhead</title>
<link rel="stylesheet" href="https://fonts.googleapis.com/css2?family=Merriweather:wght@400;700&display=swap">
<style>
  :root {
    --orange: #ee7623;
    --orange-soft: rgba(238, 118, 35, 0);
    --ink: #3b2a22;
    --paper: #ffffff;
    --label: #ffffff;
  }
  html, body {
    margin: 0;
    padding: 0;
    overflow: hidden;
    background: var(--paper);
  }
  .letterhead {
    position: relative;
    width: 870px;
    height: 1200px;
    background: var(--paper);
    font-family: "Merriweather", Georgia, serif;
    color: var(--ink);
    overflow: hidden;
  }
  .brand {
    position: absolute;
    left: 32px;
    top: 30px;
    display: flex;
    align-items: center;
    gap: 14px;
  }
  .brand-square {
    width: 22px;
    height: 22px;
    background: var(--orange);
  }
  .brand-name {
    font-weight: 700;
    font-size: 40px;
    line-height: 1;
    color: var(--ink);
    letter-spacing: 0.5px;
  }
  .brand-name small {
    display: block;
    font-size: 17px;
    margin-top: 8px;
    letter-spacing: 0.3px;
  }
  .postal {
    position: absolute;
    right: 28px;
    top: 26px;
    text-align: right;
    font-style: normal;
    font-weight: 700;
    font-size: 19px;
    line-height: 30px;
    color: var(--ink);
  }
  .footer-decoration {
    position: absolute;
    left: 0;
    top: 1040px;
    width: 870px;
    height: 70px;
    background: linear-gradient(to bottom, var(--orange-soft), var(--orange));
  }
  .footer-band {
    position: absolute;
    left: 0;
    top: 1110px;
    width: 870px;
    height: 90px;
    background: var(--orange);
  }
  .contact {
    position: absolute;
    font-size: 20px;
    line-height: 29px;
    margin: 0;
  }
  .contact dt {
    display: inline;
    color: var(--label);
  }
  .contact dd {
    display: inline;
    margin: 0;
    font-weight: 700;
    color: var(--ink);
  }
  .contact-phone {
    left: 18px;
    top: 1112px;
  }
  .contact-online {
    right: 22px;
    top: 1141px;
    text-align: right;
  }
</style>
</head>
<body>
<div class="letterhead">
  <div class="brand">
    <div class="brand-square"></div>
    <div class="brand-name">Vendaro<small>Constructions Pty Ltd</small></div>
  </div>

  <address class="postal">
    PO Box 617<br>
    Ashcombe<br>
    NSW&nbsp; 2046
  </address>

  <div class="footer-decoration" role="img" aria-label="Decorative orange building silhouette band"></div>

  <div class="footer-band"></div>

  <dl class="contact contact-phone">
    <div><dt>Tel: </dt><dd>0295550184</dd></div>
    <div><dt>Fax: </dt><dd>0295550196</dd></div>
    <div><dt>Mobile: </dt><dd>0400555318</dd></div>
  </dl>

  <dl class="contact contact-online">
    <div><dt>Email: </dt><dd>m.vendaro@mailhub.com.au</dd></div>
    <div><dt>Web: </dt><dd>www.vendaroconstructions.com.au</dd></div>
  </dl>
</div>
</body>
</html>
```